Local water manufacturing needs a re-design to an existing label design.

We need to change an existing label design for an established water manufacturing company located in the Bahamas. We are expanding into a new 1.5L size product and would like to do so with an updated label design that incorporates an animated pink conch shell (sample included) with at least one other bright color to match the existing blue background and the pink conch shell. The final design should convey an island feel and vibe. The existing label is only a suggestion. The entire label can be completely changed.

Target Market(s)

Hotels, tourist

Industry/Entity Type

Water Manufacturing

Requirements
Must have
• Bright color that matches blue cap and pink conch shell
Nice to have
• Simple design with sleek modern look.

```html
<!DOCTYPE html>
<html lang="en">
<head>
<meta charset="utf-8">
<title>Marisol Purified Water Label</title>
<link rel="stylesheet" href="https://fonts.googleapis.com/css2?family=Poppins:wght@400;600;700&family=Oswald:wght@500;700&display=swap">
<style>
  :root {
    --pink: #d2177d;
    --pink-dark: #b80f6a;
    --navy: #1d2a58;
    --sky-top: #f4fafd;
    --sky-low: #bfe3f1;
    --sea-deep: #1a93bb;
    --sea-light: #43c3d2;
    --surf: #bfeceb;
    --sand: #f4e0bd;
    --sand-deep: #ecd0a0;
    --shell: #f2b7a8;
    --white: #ffffff;
  }
  * { margin: 0; padding: 0; box-sizing: border-box; }
  html, body { width: 720px; height: 1200px; overflow: hidden; background: #ffffff; }
  .label {
    position: relative;
    width: 720px; height: 1200px;
    overflow: hidden;
    font-family: "Poppins", sans-serif;
    color: var(--navy);
  }
  .beach-scene {
    position: absolute; inset: 0;
    background: linear-gradient(to bottom,
      var(--sky-top) 0%, var(--sky-low) 45%,
      var(--sea-deep) 48%, var(--sea-light) 54%,
      var(--surf) 58.5%, var(--sand) 61%, var(--sand-deep) 100%);
  }
  .conch-art {
    position: absolute; left: 70px; top: 690px;
    width: 260px; height: 230px;
    border-radius: 48% 52% 40% 60%;
    background: radial-gradient(circle at 45% 45%, #f7cfc2, var(--shell) 60%, #e79a8c);
  }
  .shore-decor { position: absolute; border-radius: 50%; background: #e9c48f; opacity: .7; }
  .shore-decor.starfish-left { left: 0; top: 960px; width: 150px; height: 190px; }
  .shore-decor.shell-middle { left: 290px; top: 1035px; width: 120px; height: 110px; }
  .shore-decor.shell-right { left: 500px; top: 985px; width: 130px; height: 140px; }

  /* rotated print layer: reads bottom-to-top */
  .print-layer {
    position: absolute; left: 0; top: 1200px;
    width: 1200px; height: 720px;
    transform: rotate(-90deg); transform-origin: top left;
  }
  .brand-band {
    position: absolute; left: 408px; top: 0;
    width: 792px; height: 228px;
    background: linear-gradient(to bottom, var(--pink), var(--pink-dark));
    border-radius: 60px 0 0 0;
  }
  .brand-name {
    position: absolute; left: 460px; top: 30px;
    font-family: "Poppins", sans-serif; font-weight: 700;
    font-size: 136px; line-height: 170px; color: var(--white);
    letter-spacing: 2px;
  }
  .product { position: absolute; left: 648px; top: 326px; }
  .product-title {
    font-family: "Oswald", sans-serif; font-weight: 500;
    font-size: 38px; line-height: 44px; letter-spacing: 1px; color: var(--navy);
  }
  .product-sub {
    font-family: "Oswald", sans-serif; font-weight: 500;
    font-size: 26px; line-height: 34px; letter-spacing: 4px; color: var(--navy);
  }
  .bottler { position: absolute; left: 648px; top: 450px; font-size: 15px; line-height: 24px; }
  .bottler h3, .contact h3 { font-size: 19px; font-weight: 700; line-height: 26px; }
  .contact { position: absolute; left: 648px; top: 568px; font-size: 18px; line-height: 28px; }
  .nutrition {
    position: absolute; left: 72px; top: 238px;
    width: 290px; font-size: 11px; line-height: 17px;
  }
  .nutrition h2 {
    font-family: "Oswald", sans-serif; font-weight: 700;
    font-size: 38px; line-height: 42px; border-bottom: 3px solid var(--navy);
  }
  .nutrition .row { display: flex; justify-content: space-between; border-bottom: 1px solid var(--navy); }
  .nutrition .row.thick { border-bottom-width: 4px; }
  .nutrition .note { font-size: 9px; line-height: 13px; padding-top: 3px; }
</style>
</head>
<body>
<div class="label">
  <div class="beach-scene" role="img" aria-label="Illustrated tropical beach: pale sky, turquoise sea and sandy shore"></div>
  <div class="conch-art" role="img" aria-label="Illustration of a pink conch shell on the sand"></div>
  <div class="shore-decor starfish-left" role="img" aria-label="Sketched starfish on the sand"></div>
  <div class="shore-decor shell-middle" role="img" aria-label="Sketched seashell"></div>
  <div class="shore-decor shell-right" role="img" aria-label="Sketched seashells and starfish"></div>

  <div class="print-layer">
    <div class="brand-band"></div>
    <div class="brand-name">Marisol</div>

    <div class="product">
      <div class="product-title">PURIFIED WATER</div>
      <div class="product-sub">MINERALS ADDED</div>
    </div>

    <div class="bottler">
      <h3>Bottled by:</h3>
      <p>MW Ltd. t/a Marisol Water &amp; Tide Water.</p>
      <p>PO BOX TB-20418</p>
    </div>

    <div class="contact">
      <h3>Call For More Info:</h3>
      <p>sales:555-0148</p>
      <p>office:555-0172</p>
    </div>

    <div class="nutrition">
      <h2>Nutrition Facts</h2>
      <div class="row"><span>Serving Size 1 bottle</span><span></span></div>
      <div class="row thick"><span>Servings Per Container 1</span><span></span></div>
      <div class="row"><span>Amount Per Serving</span><span>% Daily Value*</span></div>
      <div class="row"><span>Calories 0</span><span></span></div>
      <div class="row"><span>Total Fat 0g</span><span>0%</span></div>
      <div class="row"><span>Saturated Fat 0g</span><span>0%</span></div>
      <div class="row"><span>Sodium 0mg</span><span>0%</span></div>
      <div class="row"><span>Total Carb 0g</span><span>0%</span></div>
      <div class="row"><span>Sugars 0g</span><span></span></div>
      <div class="row thick"><span>Protein 0g</span><span></span></div>
      <p class="note">*Percent Daily Values are based on a 2,000 calorie diet.</p>
    </div>
  </div>
</div>
</body>
</html>
```